Email Preference Page Design

We are looking for a 2 page design for our users to edit their email preferences and submit friend referrals. You can find the fuctionality, content and text here:

https://brightvanta.mailrelayhub.example/app/linkClick/7281/5fa9c1d3b07e442b/28374615/9bd4e01a7c3f2a65

* the shipping and billing address might be different so you need to show the billing if the "same as shipping" box is not checked. It can auto-hide like the page above shows if that fits your design.

* when the "unsubscribe from all email lists" box is selected, all the other checkbox options will hide as in the example page. We need you to show us what the site will look like with and without that checkbox selected.

We want to match these two pages to the general feel of these website pages:

www.brightvanta.com
and
free.brightvanta.com

The page should be very clean and tight. Project is for design only but must be able to be implemented in html showing button and checkbox states. Technically this must be two pages for our system - one for all the user info and one for individual email referrals (see example above).

Target Market(s)

video professionals

Industry/Entity Type

Shipping

Requirements
Must have
• our logo (see numerous versions attached)
well designed header
well designed sections
clean editable text
tight layout
html friendly
easy to understand
2 pages
Nice to have
• custom checkboxes and radio buttons

```html
<!DOCTYPE html>
<html lang="en">
<head>
<meta charset="utf-8">
<title>Brightvanta – Communication Preferences</title>
<link href="https://fonts.googleapis.com/css2?family=Open+Sans:ital,wght@0,400;0,600;0,700;1,400&family=Exo+2:wght@300;400&display=swap" rel="stylesheet">
<style>
  :root {
    --ink: #1b2a38;
    --navy: #192734;
    --orange: #f15a22;
    --field-border: #c9cdd1;
    --field-text: #5b6168;
    --muted: #8a8f95;
    --grey-band: #e6e7ea;
    --white: #ffffff;
    --focus: #cfe3ea;
  }
  * { box-sizing: border-box; margin: 0; padding: 0; }
  html, body { width: 1200px; height: 2951px; overflow: hidden; }
  body {
    position: relative;
    background: var(--white);
    font-family: "Open Sans", Arial, sans-serif;
    color: var(--ink);
  }

  /* Brand */
  .brand {
    position: absolute; top: 22px; left: 0; width: 1200px;
    display: flex; justify-content: center; align-items: center; gap: 24px;
  }
  .brand-dot { width: 70px; height: 70px; border-radius: 50%; background: var(--ink); }
  .brand-name { font-size: 100px; font-weight: 600; line-height: 1.1; color: var(--ink); letter-spacing: 1px; }

  /* Hero band */
  .hero {
    position: absolute; top: 167px; left: 0; width: 1200px; height: 236px;
    background: radial-gradient(ellipse at 55% 55%, #f7a23a 0%, #e0651c 35%, #9a3310 70%, #3a1a10 100%);
  }
  .hero-title {
    position: absolute; top: 218px; left: 0; width: 1200px; text-align: center;
    font-family: "Exo 2", Arial, sans-serif; font-weight: 300;
    font-size: 51px; line-height: 67px; color: var(--white); text-transform: uppercase;
  }

  /* Divider */
  .divider-line { position: absolute; top: 530px; height: 3px; background: var(--ink); }
  .divider-line.left { left: 49px; width: 514px; }
  .divider-line.right { left: 641px; width: 352px; }
  .divider-badge { position: absolute; top: 492px; left: 563px; width: 79px; height: 79px; border-radius: 50%; background: var(--ink); }
  .required-note { position: absolute; top: 510px; left: 1015px; font-size: 17px; color: var(--muted); }

  /* Section headers */
  .section-head {
    position: absolute; height: 65px; background: var(--navy); color: var(--white);
    font-family: "Exo 2", Arial, sans-serif; font-size: 31px; line-height: 65px; padding-left: 26px;
    clip-path: polygon(0 0, 100% 0, calc(100% - 14px) 50%, 100% 100%, 0 100%);
  }
  .section-head.contact { top: 653px; left: 49px; width: 512px; }
  .section-head.shipping { top: 653px; left: 639px; width: 508px; }

  /* Fields */
  .field {
    position: absolute; height: 52px; border: 2px solid var(--field-border); background: var(--white);
    font-size: 22px; color: var(--field-text); line-height: 48px; padding-left: 18px;
  }
  .field.focused { border-color: var(--focus); }
  .field.select::after {
    content: "▼"; position: absolute; right: 0; top: 0; width: 40px; height: 100%;
    border-left: 2px solid var(--field-border); text-align: center; font-size: 16px; color: var(--muted);
  }
  .plus { position: absolute; font-size: 20px; color: var(--muted); }
  .hint { position: absolute; font-size: 17px; color: var(--field-text); }

  /* Checkboxes */
  .box {
    display: inline-block; width: 27px; height: 27px; border: 2px solid var(--field-border);
    border-radius: 4px; background: var(--white); flex-shrink: 0;
  }
  .billing-same { position: absolute; top: 738px; left: 631px; display: flex; gap: 12px; font-size: 29px; line-height: 36px; color: var(--ink); }
  .billing-same .box { margin-top: 6px; }

  /* Preferences band */
  .prefs { position: absolute; top: 1489px; left: 0; width: 1200px; height: 1462px; background: var(--grey-band); }
  .subscribe { position: absolute; top: 1567px; left: 51px; display: flex; gap: 12px; font-size: 29px; line-height: 36px; }
  .subscribe .box { margin-top: 4px; }
  .subscribe-note { position: absolute; top: 1605px; left: 90px; font-size: 28px; font-style: italic; color: var(--ink); }
  .filter-heading { position: absolute; top: 1673px; left: 49px; font-size: 29px; font-weight: 700; color: var(--orange); }

  .panel { position: absolute; top: 1743px; height: 983px; background: var(--white); }
  .panel.products { left: 49px; width: 543px; }
  .panel.interests { left: 614px; width: 543px; }
  .panel-head { height: 118px; background: var(--navy); color: var(--white); font-size: 29px; line-height: 36px; padding: 23px 36px 0 36px; }
  .options { list-style: none; padding: 48px 0 0 32px; display: flex; flex-direction: column; gap: 27px; }
  .options li { display: flex; gap: 16px; font-size: 21px; line-height: 27px; color: var(--ink); }
  .options li.tight { margin-bottom: -7px; }
  .options li.unsubscribe { margin-top: 22px; color: var(--orange); font-weight: 700; font-size: 22px; }

  .submit {
    position: absolute; top: 2773px; left: 49px; width: 354px; height: 83px; border: 0;
    background: var(--orange); color: var(--white); font-family: "Open Sans", Arial, sans-serif;
    font-size: 39px; font-weight: 700; text-align: left; padding-left: 46px;
    clip-path: polygon(0 0, 100% 0, calc(100% - 26px) 50%, 100% 100%, 0 100%);
  }
</style>
</head>
<body>

  <header>
    <div class="brand">
      <span class="brand-dot"></span>
      <span class="brand-name">brightvanta</span>
    </div>
    <div class="hero" role="img" aria-label="Fiery orange abstract motion-loop backdrop"></div>
    <h1 class="hero-title">Communication<br>Preferences</h1>
  </header>

  <div class="divider-line left"></div>
  <div class="divider-badge"></div>
  <div class="divider-line right"></div>
  <div class="required-note">Required Fields*</div>

  <!-- Contact info -->
  <div class="section-head contact">Contact Info</div>
  <div class="field" style="top:747px;left:49px;width:512px">First Name*</div>
  <div class="field focused" style="top:806px;left:49px;width:512px">Last Name*</div>
  <div class="field" style="top:865px;left:49px;width:512px">Email *</div>
  <div class="field" style="top:924px;left:49px;width:512px">Phone</div>
  <div class="field" style="top:983px;left:49px;width:512px">Address 1</div>
  <div class="field" style="top:1043px;left:49px;width:512px">Address 2</div>
  <div class="field" style="top:1103px;left:49px;width:512px">Address 3</div>
  <div class="field" style="top:1163px;left:49px;width:512px">City</div>
  <div class="field select" style="top:1223px;left:49px;width:512px;height:57px;line-height:53px">Select Country</div>
  <div class="field" style="top:1282px;left:49px;width:512px">State</div>
  <div class="field" style="top:1343px;left:49px;width:226px">11111</div>
  <div class="plus" style="top:1355px;left:293px">+</div>
  <div class="field" style="top:1343px;left:319px;width:242px">1111</div>
  <div class="hint" style="top:1399px;left:49px">Postal Code + 4</div>

  <!-- Shipping address -->
  <div class="section-head shipping">Shipping Address</div>
  <label class="billing-same"><span class="box"></span><span>Billing address is same as<br>shipping address</span></label>
  <div class="field" style="top:859px;left:639px;width:508px">Street Address 1</div>
  <div class="field" style="top:918px;left:639px;width:508px">Street Address 2</div>
  <div class="field" style="top:977px;left:639px;width:508px">Street Address 3</div>
  <div class="field" style="top:1036px;left:639px;width:508px">City</div>
  <div class="field select" style="top:1098px;left:639px;width:508px;height:56px;line-height:52px">Select Country</div>
  <div class="field" style="top:1156px;left:639px;width:508px">State</div>
  <div class="field" style="top:1217px;left:639px;width:226px">44444</div>
  <div class="plus" style="top:1229px;left:873px">+</div>
  <div class="field" style="top:1217px;left:899px;width:248px">2222</div>
  <div class="hint" style="top:1273px;left:639px">Postal Code + 4</div>

  <!-- Preferences -->
  <section class="prefs"></section>
  <label class="subscribe"><span class="box"></span><span>Subscribe me to your general email list</span></label>
  <p class="subscribe-note">This monthly email includes free video loops and VIP sale notices</p>
  <h2 class="filter-heading">Help us filter our emails so we only sending relevant information to you</h2>

  <div class="panel products">
    <div class="panel-head">Send me emails about these<br>product types:</div>
    <ul class="options">
      <li class="tight"><span class="box"></span><span>Low energy motion loops</span></li>
      <li class="tight"><span class="box"></span><span>High energy motion loops</span></li>
      <li><span class="box"></span><span>Timelapse footage</span></li>
      <li><span class="box"></span><span>Low energy motion loops</span></li>
      <li><span class="box"></span><span>High energy motion loops</span></li>
      <li><span class="box"></span><span>Timelapse footage</span></li>
      <li><span class="box"></span><span>Worship or wedding motion loops</span></li>
      <li><span class="box"></span><span>Pre-mixed DVDs and BluRay</span></li>
      <li><span class="box"></span><span>Entertainment lasers for concerts<br>and clubs</span></li>
      <li><span class="box"></span><span>Entertainment lasers for text &amp; logo<br>display</span></li>
      <li><span class="box"></span><span>Custom logo animation services</span></li>
      <li><span class="box"></span><span>Video software for creating video<br>animations</span></li>
      <li><span class="box"></span><span>Video software for live performance )</span></li>
    </ul>
  </div>

  <div class="panel interests">
    <div class="panel-head">I am Involved in or have<br>interest in:</div>
    <ul class="options">
      <li class="tight"><span class="box"></span><span>VJing (live performance video)</span></li>
      <li class="tight"><span class="box"></span><span>DJing (live performance audio+video)</span></li>
      <li><span class="box"></span><span>Performing in a band</span></li>
      <li><span class="box"></span><span>Video editing</span></li>
      <li><span class="box"></span><span>Corporate presentations</span></li>
      <li><span class="box"></span><span>Worship video services</span></li>
      <li><span class="box"></span><span>Lasers for entertainment &amp; branding</span></li>
      <li><span class="box"></span><span>Special offers from BrightVanta partners</span></li>
      <li class="unsubscribe"><span class="box"></span><span>Unsubscribe from all email lists</span></li>
    </ul>
  </div>

  <button class="submit" type="submit">Submit Now</button>

</body>
</html>
```